Business card for marketing analytics company

Need a business card for new company. I have a logo already that I want to be built into the card and should use those colours

Company is called steered by tallies
Design must bring steered by tallies to life not be a card that could be for anyone with a logo put on it.

Like the front to be fairly clean and uncluttered bringing the logo out with a suitable design on the back of the card.

The logo represents a compass and business growth so those themes along with numbers, analytics , data are appropriate.
I'm often working with creative industries so also needs to reflect the creative side of analytics rather than be very corporate looking.

Target Market(s)

Ad agency, media agency, consumer goods clients

Industry/Entity Type

Market Research

Contact Information for Business Card

Needs to include name, title, email and phone number

Colors
f78f20
f68d4d
ec1f27

Requirements
Must have
• Must bring steered by tallies to life not be a card that could be for anyone with a logo put on it.
• Logo, Correct colours
• Like a design on the back that relates to company name
• Designs for both sides
Should not have
• Please do not just submit logo and a coloured card.
• It needs to have a design element to it
• No black background
• No clear cards - needs front & back

```html
<!DOCTYPE html>
<html lang="en">
<head>
<meta charset="utf-8">
<title>Steered by Tallies – Business Card</title>
<link href="https://fonts.googleapis.com/css2?family=Exo+2:wght@400;600;700&display=swap" rel="stylesheet">
<style>
  :root {
    --backdrop: #d8d9dc;
    --card: #38383b;
    --card-edge: #2c2c2f;
    --white: #f4f4f4;
    --grey: #c2c2c4;
    --faint: #46464a;
    --faint-soft: #404044;
    --orange: #f78f20;
    --orange-soft: #f68d4d;
    --red: #ec1f27;
  }
  html, body {
    margin: 0;
    width: 1200px;
    height: 1000px;
    overflow: hidden;
    background: var(--backdrop);
    font-family: "Exo 2", "Helvetica Neue", Arial, sans-serif;
  }
  .canvas {
    position: relative;
    width: 1200px;
    height: 1000px;
  }
  .card {
    position: absolute;
    width: 560px;
    height: 320px;
    background: var(--card);
    border-radius: 4px;
    box-shadow: 0 6px 0 var(--card-edge), 0 18px 36px rgba(0,0,0,.25);
    overflow: hidden;
  }
  .card--back { left: 580px; top: 110px; }
  .card--front { left: 70px; top: 470px; }

  /* back side */
  .back-brand {
    position: absolute;
    left: 36px;
    top: 36px;
    display: flex;
    align-items: center;
    gap: 12px;
  }
  .brand-dot {
    width: 30px;
    height: 30px;
    border-radius: 50%;
    border: 3px solid var(--red);
    box-sizing: border-box;
  }
  .brand-name {
    margin: 0;
    color: var(--orange);
    font-weight: 600;
    font-size: 18px;
    line-height: 1.05;
  }
  .back-emblem {
    position: absolute;
    right: 30px;
    top: 40px;
    width: 250px;
    height: 250px;
    border-radius: 50%;
    border: 8px solid var(--faint);
    box-sizing: border-box;
    background: radial-gradient(circle at 50% 50%, var(--faint-soft) 0%, var(--card) 70%);
  }

  /* front side */
  .front-title {
    position: absolute;
    left: 36px;
    top: 28px;
    margin: 0;
    color: var(--white);
    font-weight: 600;
    font-size: 36px;
    line-height: 1.0;
  }
  .person {
    position: absolute;
    left: 36px;
    top: 132px;
  }
  .person-name {
    margin: 0;
    color: var(--orange);
    font-weight: 700;
    font-size: 22px;
    letter-spacing: .5px;
  }
  .person-role {
    margin: 2px 0 0;
    color: var(--grey);
    font-size: 13px;
    letter-spacing: .5px;
  }
  .contact {
    position: absolute;
    left: 36px;
    top: 206px;
    margin: 0;
    padding: 0;
    list-style: none;
    color: var(--grey);
    font-size: 13px;
  }
  .contact li {
    display: flex;
    align-items: center;
    gap: 10px;
    margin-bottom: 7px;
  }
  .contact svg { width: 11px; height: 11px; }
  .contact .accent { color: var(--orange); }
  .front-emblem {
    position: absolute;
    right: 40px;
    top: 44px;
    width: 240px;
    height: 240px;
    border-radius: 50%;
    border: 9px solid var(--red);
    box-sizing: border-box;
    background: radial-gradient(circle at 50% 50%, rgba(247,143,32,.28) 0%, rgba(236,31,39,.08) 60%, transparent 72%);
  }
</style>
</head>
<body>
<main class="canvas">

  <section class="card card--back" aria-label="Card back">
    <div class="back-brand">
      <span class="brand-dot"></span>
      <p class="brand-name">Steered by<br>Tallies</p>
    </div>
    <div class="back-emblem" role="img" aria-label="Large faint compass-and-growth emblem watermark"></div>
  </section>

  <section class="card card--front" aria-label="Card front">
    <h1 class="front-title">Steered by<br>Tallies</h1>
    <div class="person">
      <p class="person-name">DANIEL BROOKS</p>
      <p class="person-role">CEO / FOUNDER</p>
    </div>
    <ul class="contact">
      <li>
        <svg viewBox="0 0 12 12"><path d="M2 1h3l1 3-1.5 1a7 7 0 0 0 2.5 2.5L8 6l3 1v3a1 1 0 0 1-1 1A9 9 0 0 1 1 2a1 1 0 0 1 1-1z" fill="var(--orange)"/></svg>
        123 456 789
      </li>
      <li>
        <svg viewBox="0 0 12 12"><rect x="1" y="2.5" width="10" height="7" rx="1" fill="none" stroke="var(--orange)" stroke-width="1.4"/><path d="M1.5 3l4.5 3.5L10.5 3" fill="none" stroke="var(--orange)" stroke-width="1.2"/></svg>
        uname@email.com
      </li>
      <li>
        <svg viewBox="0 0 12 12"><circle cx="6" cy="6" r="4.5" fill="none" stroke="var(--orange)" stroke-width="1.4"/><path d="M1.5 6h9M6 1.5v9" stroke="var(--orange)" stroke-width="1"/></svg>
        <span>www.<span class="accent">websitename</span>.com</span>
      </li>
    </ul>
    <div class="front-emblem" role="img" aria-label="Large compass-and-growth emblem in red and orange"></div>
  </section>

</main>
</body>
</html>
```